Business Card for Fashion House

We need a business card design for our personalize fashion service for our customers. the business card should reflect reliability, luxury and creativity.
The brand Gravetto is extracted from "Graceful Velvetto"; Gravetto provides fashion designs sprinkled with luxury and style tailored for our elite clients character profile.
Gravetto is created for those who embody class and elegance with a passion for style.
Target Market(s)
Affluent Customers
Industry/Entity Type
Fashion
Contact Information for Business Card
Samira Haddadin
Fashion Designer
Telephone: +971 4 555 0192
Mobile +971 50 555 0147
Emal info@gravetto-example.com
Website www.gravetto-example.com
Social Media Youtube g+ Facebook Instagram Pin /gravetto
Font styles to use
Other font styles liked:
- Audrey provided
Look and feel
Each slider illustrates characteristics of the customer's brand and the style your logo design should communicate.

```html
<!DOCTYPE html>
<html lang="en">
<head>
<meta charset="utf-8">
<title>Gravetto — Business Card</title>
<link href="https://fonts.googleapis.com/css2?family=Cormorant+Garamond:ital,wght@0,400;0,500;1,500&display=swap" rel="stylesheet">
<style>
  :root {
    --bg: #1b1b1b;
    --card-white: #ffffff;
    --card-shade: #e9e9e9;
    --ink: #1a1a1a;
    --rule: #2a2a2a;
    --swoosh-edge: #0c0c0c;
    --swoosh-fill: #6b6b6b;
    --swoosh-light: #8a8a8a;
    --back-dark: #0e0e0e;
    --back-mid: #262626;
    --back-text: #f2f2f2;
  }
  * { box-sizing: border-box; margin: 0; padding: 0; }
  html, body {
    width: 1200px; height: 864px; overflow: hidden;
    background: var(--bg);
    font-family: "Cormorant Garamond", Georgia, serif;
  }
  .canvas { position: relative; width: 1200px; height: 864px; }

  .card { position: absolute; width: 560px; height: 320px; overflow: hidden; box-shadow: 0 18px 40px rgba(0,0,0,.6); }

  /* Front */
  .card-front {
    left: 110px; top: 430px;
    background: linear-gradient(160deg, var(--card-white) 55%, var(--card-shade));
    color: var(--ink);
  }
  .card-front .swoosh { position: absolute; inset: 0; }
  .top-rule { position: absolute; left: 0; top: 44px; width: 400px; height: 1.5px; background: var(--rule); }
  .holder { position: absolute; right: 28px; top: 30px; text-align: right; }
  .holder-name { font-style: italic; font-weight: 500; font-size: 19px; letter-spacing: 1px; }
  .holder-role { font-style: italic; font-weight: 500; font-size: 14px; letter-spacing: .5px; margin-top: 2px; }
  .wordmark {
    position: absolute; left: 34px; top: 150px;
    display: flex; align-items: center; gap: 12px;
    font-weight: 500; font-size: 28px; letter-spacing: 8px; text-transform: uppercase;
  }
  .wordmark-dot { width: 12px; height: 12px; border-radius: 50%; background: var(--ink); }
  .contacts {
    position: absolute; right: 24px; top: 170px;
    list-style: none; text-align: right;
    font-size: 14px; font-weight: 500; letter-spacing: .8px; color: var(--ink);
  }
  .contacts li { display: flex; justify-content: flex-end; align-items: center; gap: 8px; height: 24px; }
  .contacts svg { width: 13px; height: 13px; flex: none; }

  /* Back */
  .card-back {
    left: 600px; top: 120px;
    background: var(--back-dark);
  }
  .back-texture {
    position: absolute; inset: 0;
    background: linear-gradient(115deg, var(--back-dark) 0%, var(--back-mid) 45%, var(--back-dark) 70%);
  }
  .back-wordmark {
    position: absolute; right: 34px; bottom: 30px;
    font-weight: 500; font-size: 22px; letter-spacing: 7px; text-transform: uppercase;
    color: var(--back-text);
  }
</style>
</head>
<body>
<main class="canvas">

  <section class="card card-back" aria-label="Card back">
    <div class="back-texture" role="img" aria-label="Tonal repeating brand pattern on black"></div>
    <div class="back-wordmark">Gravetto</div>
  </section>

  <section class="card card-front" aria-label="Card front">
    <svg class="swoosh" viewBox="0 0 560 320" preserveAspectRatio="none" aria-hidden="true">
      <defs>
        <linearGradient id="swooshFill" x1="0" y1="0" x2="1" y2="1">
          <stop offset="0" stop-color="var(--swoosh-light)"/>
          <stop offset="1" stop-color="var(--swoosh-fill)"/>
        </linearGradient>
      </defs>
      <path d="M286 320 C300 200 420 122 560 112 L560 320 Z" fill="var(--swoosh-edge)"/>
      <path d="M304 320 C318 212 430 138 560 128 L560 320 Z" fill="url(#swooshFill)"/>
    </svg>

    <div class="top-rule"></div>
    <div class="holder">
      <p class="holder-name">Samira Haddadin</p>
      <p class="holder-role">Fashion Designer</p>
    </div>

    <div class="wordmark"><span class="wordmark-dot"></span>Gravetto</div>

    <ul class="contacts">
      <li>+971 4 555 0192
        <svg viewBox="0 0 14 14"><circle cx="7" cy="7" r="6.2" fill="none" stroke="currentColor"/><path d="M4 5.5c0-1 1-1.5 3-1.5s3 .5 3 1.5M4.5 10h5l-.6-3.5h-3.8z" fill="none" stroke="currentColor" stroke-width="1"/></svg>
      </li>
      <li>+971 50 555 0147
        <svg viewBox="0 0 14 14"><circle cx="7" cy="7" r="6.2" fill="none" stroke="currentColor"/><rect x="5" y="3.5" width="4" height="7" rx=".8" fill="none" stroke="currentColor"/></svg>
      </li>
      <li>info@gravetto-example.com
        <svg viewBox="0 0 14 14"><circle cx="7" cy="7" r="6.2" fill="none" stroke="currentColor"/><rect x="3.8" y="4.8" width="6.4" height="4.4" fill="none" stroke="currentColor"/><path d="M3.8 4.8 7 7.4l3.2-2.6" fill="none" stroke="currentColor"/></svg>
      </li>
      <li>www.gravetto-example.com
        <svg viewBox="0 0 14 14"><circle cx="7" cy="7" r="6.2" fill="none" stroke="currentColor"/><circle cx="7" cy="7" r="3.6" fill="none" stroke="currentColor"/><path d="M3.4 7h7.2M7 3.4v7.2" stroke="currentColor"/></svg>
      </li>
    </ul>
  </section>

</main>
</body>
</html>
```